2 Fold Brochure

We are a spa looking to create a professional elegant two fold brochure for a spa mainly black and white with a splash of lime green.
Look and feel: chic, modern, and spa-ish.

The front will include an image and also it should say: (somewhere under the photo) wherever you think it will look nice.
Skin Tightening
Cellulite Reduction
Body Contouring

The second Page:
Bipolar Radiofrequency(bolded): for immediate face lifting, tone and a complete new younger looking skin!
Multipolar Radiofrequency(bolded): with Vacuum system for body contour, cellulite and fat detachment from adipose tissue.
Cavitation with red LED to treat face and small areas of the body. Red LED light stimulates collagen synthesis.

Ultra Cavitation will sculpt, treat fat, cellulite and improve body shape! It does NOT involve surgery. There is no need for anesthesia, hospital stay or time off from work. Ultra cavitation will promote microscopic air bubbles to surround the lipocyte(fat cell) membranes and with its resonant frequency, the bubbles cause a high enough pressure to break up fat instantly. These broken lipocytes are then safely metabolized out of the human body.

PRESSOTHERAPY: A Complete Body Detox! Pressortherapy based on air pressure, promotes lymphatic drainage. It aslo has infrared system for body heat and electro muscle stimulation system.

Third Page:
Packages:

1. THE NEW FACELIFT:
*Skin Tightening
*Wrinkle Reduction
*Dark Circle Elimination
*Puffy Eye Relief

BODY SHAPING

2. BODY
*Fat Reduction
*Cellulite Reduction
*Body Firming

3. PRESSOTHERAPY (DETOX) $85
*Toxic Flushing
*Lymphatic Drainage
*Toning

5.POST PREGNANCY
*Fat Reduction
*Tummy Firming and Toning
*Cellulite Reduction
*Butt Toning

Buy 5 get 1 Free - $1,250
Buy 10 get 2 Free- $2,500

The back of the second page will include before and after photos I will be sending later. Also include the Logo in the front and by the prices. I have attached our logo.

Also we need a photo to place in the front. Something that shows face and body fat reduction.

Industry/Entity Type

Hospital

```html
<!DOCTYPE html>
<html lang="en">
<head>
<meta charset="utf-8">
<title>Lumen Day Spa – Two Fold Brochure</title>
<link href="https://fonts.googleapis.com/css2?family=Lora:ital,wght@0,600;1,500;1,600&family=Raleway:wght@400;500;600&display=swap" rel="stylesheet">
<style>
  :root{
    --bg:#ebebeb;
    --paper:#f4f0e0;
    --lime:#a9c41b;
    --lime-light:#c3d82e;
    --green:#7a9a10;
    --green-dark:#5d7a0c;
    --ink:#222;
    --grey:#6b6b63;
    --orange:#e8860f;
    --script:"Lora", Georgia, serif;
    --sans:"Raleway", Arial, sans-serif;
  }
  *{box-sizing:border-box;margin:0;padding:0}
  html,body{width:1200px;height:1000px;overflow:hidden}
  body{background:var(--bg);font-family:var(--sans);color:var(--ink);position:relative}
  .spread{position:absolute;top:290px;display:flex;box-shadow:0 16px 30px rgba(0,0,0,.12)}
  .spread--outside{left:40px}
  .spread--inside{left:620px}
  .page-label{position:absolute;top:-42px;width:280px;text-align:center;font-size:19px;color:#222}
  .page{position:relative;width:270px;height:420px;background:var(--paper);overflow:hidden}
  .page + .page{border-left:1px solid #ddd8c4}
  .wave{position:absolute;left:0;bottom:0;width:100%;height:110px}
  .wave--top{top:0;bottom:auto;height:80px}
  .dot{position:absolute;border-radius:50%;background:var(--lime)}
  .photo{position:absolute;border-radius:6px}

  /* brand */
  .brand{position:absolute;display:flex;align-items:center;gap:5px;z-index:2}
  .brand__mark{width:14px;height:14px;border-radius:50%;background:var(--ink)}
  .brand__name{font-family:var(--script);font-weight:600;font-size:12px;color:var(--ink);line-height:1.05;width:52px}

  /* back cover */
  .price-list{position:absolute;left:104px;top:16px;list-style:none}
  .price-list li{font-family:var(--script);font-style:italic;font-weight:600;font-size:11.5px;line-height:18px}
  .price-list span{color:var(--green)}
  .back-photo{left:20px;top:92px;width:232px;height:240px;border-top:6px solid var(--lime-light);background:linear-gradient(90deg,#b88a6a,#d3a587 30%,#5a5fb0 48%,#fff 50%,#4b4fa6 52%,#c99877 75%,#a97c60)}

  /* front cover */
  .cover-photo{left:0;top:56px;width:270px;height:280px;border-radius:0;background:linear-gradient(135deg,#c9d9a6,#e8cbb5 45%,#f1d6c2 70%,#d9c2ae)}
  .tagline{position:absolute;right:14px;bottom:12px;z-index:2;text-align:right;font-family:var(--script);font-style:italic;font-weight:600;font-size:11px;color:var(--ink);line-height:18px}
  .tagline em{font-size:14px;color:var(--green);font-style:italic}

  /* inside */
  .inside{position:absolute;left:14px;top:36px;right:14px}
  .treat h2{font-family:var(--script);font-weight:600;font-style:italic;font-size:14px;color:var(--ink);margin-top:10px}
  .treat h2 em{color:var(--lime);font-weight:500}
  .treat h2.solo{color:var(--lime);font-weight:500}
  .treat p{font-size:6.3px;line-height:9px;color:var(--grey);margin-top:3px}
  .treat--split{display:flex;gap:8px}
  .treat--split .col{flex:1}
  .ba{width:104px;flex:none;margin-top:4px}
  .ba__tag{background:#fff;text-align:center;font-size:6.5px;font-weight:600;letter-spacing:.5px;padding:1px 0}
  .ba__img{height:68px;background:linear-gradient(180deg,#8a5a3c,#c89470 60%,#efe4d9)}

  .packages{position:absolute;left:10px;top:36px;right:10px}
  .pkg{display:flex;gap:8px;align-items:flex-start;margin-bottom:8px;height:62px}
  .pkg__img{width:104px;height:60px;flex:none;border-radius:6px;border:2px solid var(--lime-light)}
  .pkg h3{font-family:var(--script);font-weight:600;font-size:11px;font-style:italic}
  .pkg h3 em{color:var(--lime);font-weight:500;font-size:13px}
  .pkg ul{list-style:none;font-size:6.3px;color:var(--grey);line-height:8.5px;margin-top:3px}
  .offers{font-family:var(--script);font-style:italic;font-size:9px;font-weight:600;line-height:13px;margin-top:2px}
  .offers b{color:var(--orange)}
  .offers i{color:var(--green)}
</style>
</head>
<body>

<section class="spread spread--outside">
  <span class="page-label" style="left:0">Page 4</span>
  <span class="page-label" style="left:270px">Page 1</span>

  <article class="page page--back">
    <div class="brand" style="left:14px;top:22px">
      <span class="brand__mark"></span><span class="brand__name">Lumen Day Spa</span>
    </div>
    <ul class="price-list">
      <li>The New Facelift <span>- $109</span></li>
      <li>Body Shaping <span>- $220</span></li>
      <li>The New Facelift <span>- $100</span></li>
      <li>The New Facelift <span>- $300</span></li>
    </ul>
    <div class="photo back-photo" role="img" aria-label="Before and after photos of cellulite reduction on the back of the thighs"></div>
    <svg class="wave" viewBox="0 0 270 110" preserveAspectRatio="none">
      <path d="M0 20 C80 60 180 70 270 40 V110 H0Z" fill="var(--green)"/>
      <path d="M0 40 C90 80 190 85 270 60 V110 H0Z" fill="var(--lime)"/>
      <path d="M0 70 C90 95 190 100 270 85 V110 H0Z" fill="var(--paper)"/>
    </svg>
  </article>

  <article class="page page--front">
    <div class="photo cover-photo" role="img" aria-label="Photo of a woman's body showing smooth, toned skin"></div>
    <svg class="wave wave--top" viewBox="0 0 270 80" preserveAspectRatio="none">
      <path d="M0 0 H270 V10 C190 20 120 50 0 70Z" fill="var(--paper)"/>
      <path d="M110 58 C170 40 220 20 270 14 V26 C220 30 170 50 120 64Z" fill="var(--lime)"/>
    </svg>
    <div class="brand" style="left:14px;top:16px">
      <span class="brand__mark"></span><span class="brand__name">Lumen Day Spa</span>
    </div>
    <span class="dot" style="left:92px;top:20px;width:10px;height:10px"></span>
    <span class="dot" style="left:104px;top:28px;width:7px;height:7px;background:var(--green)"></span>
    <svg class="wave" viewBox="0 0 270 110" preserveAspectRatio="none">
      <path d="M0 20 C80 40 180 10 270 0 V110 H0Z" fill="var(--green)"/>
      <path d="M0 30 C90 48 190 18 270 8 V110 H0Z" fill="var(--lime)"/>
      <path d="M0 42 C90 58 190 28 270 18 V110 H0Z" fill="var(--paper)"/>
    </svg>
    <p class="tagline">Skin <em>Tightening</em><br>Cellulite <em>Reduction</em> / Body <em>Contouring</em></p>
  </article>
</section>

<section class="spread spread--inside">
  <span class="page-label" style="left:0">Page 2</span>
  <span class="page-label" style="left:270px">Page 3</span>

  <article class="page page--treatments">
    <span class="dot" style="left:132px;top:18px;width:6px;height:6px"></span>
    <span class="dot" style="left:140px;top:12px;width:9px;height:9px;background:var(--lime-light)"></span>
    <div class="inside">
      <div class="treat">
        <h2>Bipolar <em>Radiofrequency</em></h2>
        <p>for immediate face lifting, tone and a complete new younger looking skin!</p>
      </div>
      <div class="treat">
        <h2>Multipolar <em>Radiofrequency</em></h2>
        <div class="treat--split">
          <div class="col">
            <p>with Vacuum system for body contour, cellulite and fat detachment from adipose tissue.</p>
            <p>Cavitation with red LED to treat face and small areas of the body. Red LED light stimulates collagen synthesis.</p>
            <p>Ultra Cavitation will sculpt, treat fat, cellulite and improve body shape! It does NOT involve surgery. There is no need for anesthesia, hospital stay or time off from work. Ultra cavitation will promote microscopic air bubbles to surround the lipocyte (fat cell) membranes and with its resonant frequency, the bubbles cause a high enough pressure to break up fat instantly. These broken lipocytes are then safely metabolized out of the human body.</p>
          </div>
          <div class="ba">
            <div class="ba__tag">BEFORE</div>
            <div class="ba__img" role="img" aria-label="Before photo of a stomach"></div>
            <div class="ba__tag">AFTER</div>
            <div class="ba__img" role="img" aria-label="After photo of a slimmer stomach"></div>
          </div>
        </div>
      </div>
      <div class="treat">
        <h2 class="solo">Pressotherapy</h2>
        <p>A Complete Body Detox! Pressotherapy based on air pressure, promotes lymphatic drainage. It also has infrared system for body heat and electro muscle stimulation system.</p>
      </div>
    </div>
    <svg class="wave" viewBox="0 0 270 110" preserveAspectRatio="none">
      <path d="M0 40 C80 20 180 60 270 70 V110 H0Z" fill="var(--green)"/>
      <path d="M0 50 C90 30 180 70 270 80 V110 H0Z" fill="var(--lime)"/>
    </svg>
  </article>

  <article class="page page--packages">
    <div class="packages">
      <div class="pkg">
        <div class="pkg__img" role="img" aria-label="Photo of a woman receiving a facial treatment" style="background:linear-gradient(135deg,#f4ece6,#d8b8a4)"></div>
        <div><h3>The New <em>Facelift</em></h3>
          <ul><li>Skin Tightening</li><li>Wrinkle Reduction</li><li>Dark Circle Elimination</li><li>Puffy Eye Relief</li></ul></div>
      </div>
      <div class="pkg">
        <div><h3>Body <em>Shaping</em></h3>
          <ul><li>Fat Reduction</li><li>Cellulite Reduction</li><li>Body Firming</li></ul></div>
        <div class="pkg__img" role="img" aria-label="Photo of a woman's figure before and after body shaping" style="margin-left:auto;background:linear-gradient(90deg,#eee,#7c4a7a 30%,#eee 50%,#7c4a7a 75%,#eee)"></div>
      </div>
      <div class="pkg">
        <div class="pkg__img" role="img" aria-label="Photo of a woman relaxing during a massage" style="background:linear-gradient(135deg,#7a5034,#d9b099 60%,#e9e2d6)"></div>
        <div><h3>Pressotherapy <em>(Detox) $85</em></h3>
          <ul><li>Toxic Flushing</li><li>Lymphatic Drainage</li><li>Toning</li></ul></div>
      </div>
      <div class="pkg">
        <div><h3>Post <em>Pregnancy</em></h3>
          <ul><li>Fat Reduction</li><li>Tummy Firming and Toning</li><li>Cellulite Reduction</li><li>Butt Toning</li></ul></div>
        <div class="pkg__img" role="img" aria-label="Photo of a mother with her baby at home" style="margin-left:auto;background:linear-gradient(90deg,#e9d6d0,#e06ba0 40%,#f0e8e2)"></div>
      </div>
      <p class="offers"><b>BUY</b> 5 GET 1 <i>FREE</i> - $1,250<br><b>BUY</b> 10 GET 2 <i>FREE</i> - $2,500</p>
    </div>
    <span class="dot" style="right:14px;top:60px;width:8px;height:8px"></span>
    <svg class="wave" viewBox="0 0 270 110" preserveAspectRatio="none">
      <path d="M0 60 C90 40 180 30 270 45 V110 H0Z" fill="var(--green)"/>
      <path d="M0 70 C90 52 180 44 270 58 V110 H0Z" fill="var(--lime)"/>
    </svg>
  </article>
</section>

</body>
</html>
```